Need Flyer for Our Real estate Agency

Need to run General Campaign for our agency with Start of New Year as our theme ..Must have an agent's picture on the DL..
Address:
27 / 486Brindle rd, Marsden VIC 3047
Ph:03 9412 7306
email:info@kovalinrealestate.com.au
www.kovalinrealestate.com.au
Something like as attached picture..
Target Market(s)
Home Buyers
Industry/Entity Type
Real Estate Agent
Requirements
Must have
- Our Logo Colours

```html
<!DOCTYPE html>
<html lang="en">
<head>
<meta charset="utf-8">
<title>Kovalin Real Estate – DL Flyer</title>
<link rel="stylesheet" href="https://fonts.googleapis.com/css2?family=Lato:wght@400;700;900&display=swap">
<style>
  :root {
    --navy: #1c2350;
    --blue: #1f7fc1;
    --maroon: #7a1a26;
    --cream: #f3efdc;
    --backdrop: #e7e4dd;
    --sky-top: #8fb8d6;
    --sky-low: #cfe0ea;
    --grass: #5d8a3a;
  }
  * { box-sizing: border-box; margin: 0; padding: 0; }
  html, body {
    width: 1200px; height: 858px; overflow: hidden;
    background: var(--backdrop);
    font-family: "Lato", Arial, sans-serif;
  }
  .canvas { position: relative; width: 1200px; height: 858px; }
  .flyer {
    position: absolute; left: 410px; top: 29px;
    width: 380px; height: 800px;
    background: var(--navy);
    overflow: hidden;
    box-shadow: 0 6px 24px rgba(0,0,0,.25);
  }
  .flyer-shapes { position: absolute; inset: 0; }
  .brand {
    position: absolute; top: 128px; left: 0; width: 100%;
    text-align: center; color: var(--cream);
  }
  .brand-name {
    display: inline-flex; align-items: center; gap: 12px;
    font-size: 46px; font-weight: 400; letter-spacing: 5px; line-height: 1;
  }
  .brand-mark { width: 12px; height: 12px; background: var(--cream); display: inline-block; }
  .brand-tag {
    margin-top: 8px; font-size: 11px; font-weight: 400; letter-spacing: 3px;
  }
  .agent-name {
    position: absolute; left: 0; width: 232px; top: 608px; text-align: center;
    color: var(--cream); font-weight: 900; font-size: 27px; line-height: 1;
  }
  .agent-role {
    position: absolute; left: 0; width: 232px; top: 638px; text-align: center;
    color: var(--cream); font-size: 10px; letter-spacing: .5px; line-height: 1;
  }
  .contact {
    position: absolute; left: 0; width: 100%; text-align: center; color: var(--cream);
    line-height: 1.2;
  }
  .contact-phone { top: 678px; font-size: 23px; font-weight: 700; }
  .contact-address { top: 710px; font-size: 13.5px; }
  .contact-email { top: 754px; font-size: 13.5px; }
  .contact-web { top: 774px; font-size: 13.5px; }
</style>
</head>
<body>
<main class="canvas">
  <article class="flyer">
    <svg class="flyer-shapes" width="380" height="800" viewBox="0 0 380 800" xmlns="http://www.w3.org/2000/svg">
      <defs>
        <linearGradient id="houseTones" x1="0" y1="0" x2="0" y2="1">
          <stop offset="0" stop-color="var(--sky-top)"/>
          <stop offset="0.55" stop-color="var(--sky-low)"/>
          <stop offset="0.8" stop-color="#b9b5ad"/>
          <stop offset="1" stop-color="var(--grass)"/>
        </linearGradient>
      </defs>
      <path d="M0,300 C110,245 250,250 380,180 L380,206 C250,272 110,268 0,318 Z" fill="var(--blue)"/>
      <path d="M0,312 C110,258 250,262 380,196 L380,208 C250,274 110,270 0,322 Z" fill="var(--cream)"/>
      <g role="img" aria-label="Photo of a modern two-storey family home with solar roof panels, garage and paved driveway under a blue sky">
        <path d="M0,322 C110,270 250,274 380,208 L380,530 C260,548 110,540 0,620 Z" fill="url(#houseTones)"/>
      </g>
      <path d="M0,620 C110,540 260,548 380,530 L380,548 C260,566 110,560 0,640 Z" fill="var(--blue)"/>
      <path d="M0,634 C110,554 260,562 380,544 L380,552 C260,570 110,566 0,644 Z" fill="var(--cream)" opacity=".9"/>
      <path d="M0,620 Q0,592 28,592 L292,592 L292,660 L0,660 Z" fill="var(--maroon)"/>
      <path d="M0,760 Q0,734 30,734 L350,734 Q380,734 380,760 L380,800 L0,800 Z" fill="var(--maroon)"/>
      <circle cx="300" cy="580" r="72" fill="var(--maroon)"/>
      <g role="img" aria-label="Portrait photo of the agent">
        <circle cx="300" cy="580" r="66" fill="var(--cream)"/>
      </g>
    </svg>

    <header class="brand">
      <div class="brand-name"><span class="brand-mark"></span>KOVALIN</div>
      <div class="brand-tag">REAL ESTATE</div>
    </header>

    <h2 class="agent-name">NAME HERE</h2>
    <p class="agent-role">MARKETING MANAGER</p>

    <p class="contact contact-phone">Ph:03 9412 7306</p>
    <p class="contact contact-address">27 / 486Brindle rd, Marsden VIC 3047</p>
    <p class="contact contact-email">email:info@kovalinrealestate.com.au</p>
    <p class="contact contact-web">www.kovalinrealestate.com.au</p>
  </article>
</main>
</body>
</html>
```